Graphic Design of Business Process

We require an eye-catching, sophisticated design of 2 business processes (attached), that will be used digitally AND for print (to be put on walls in our office).

The basic layout is attached. We require a creative, professional designer to re-design these so that they look appealing but still able to grasp all the information.

We will require vector files and editable project files for final delivery. You may refer to our website (quillharbourworks.com.au) for an indication of our brand.

If you have any questions, please ask.

Thank you.

```html
<!DOCTYPE html>
<html lang="en">
<head>
<meta charset="utf-8">
<title>Sales Content Funnel</title>
<link rel="stylesheet" href="https://fonts.googleapis.com/css2?family=Fira+Sans+Condensed:wght@600;700;800&family=Fira+Sans:wght@600;700&family=Poppins:wght@700&family=Quicksand:wght@400&display=swap">
<style>
  :root {
    --red: #ec4a4b;
    --orange: #f8a71d;
    --green: #4aae50;
    --blue: #2bbbd3;
    --purple: #7c60a8;
    --brown: #a3521b;
    --deep-green: #1c5f2b;
    --deep-blue: #145c79;
    --ink: #000000;
    --hero: #f4b51b;
    --hub: #3bb54a;
    --hygiene: #27a9d6;
    --paper: #ffffff;
  }
  html, body {
    margin: 0;
    padding: 0;
    overflow: hidden;
    background: var(--paper);
  }
  .canvas {
    position: relative;
    width: 958px;
    height: 1200px;
    overflow: hidden;
    background: var(--paper);
  }
  .funnel-diagram {
    position: absolute;
    left: 0;
    top: 0;
  }
  .heading { font-family: "Fira Sans Condensed", sans-serif; font-weight: 800; fill: #fff; }
  .kicker { font-family: "Fira Sans Condensed", sans-serif; font-weight: 700; }
  .point { font-family: "Fira Sans", sans-serif; font-weight: 600; }
  .tag-title { font-family: "Fira Sans", sans-serif; font-weight: 700; }

  .legend { position: absolute; left: 40px; width: 528px; height: 110px; }
  .legend-swatch { position: absolute; left: 0; top: 0; width: 59px; height: 100%; }
  .legend-rule { position: absolute; left: 59px; right: 0; bottom: 0; height: 3px; }
  .legend-title {
    position: absolute; left: 80px; top: -8px; margin: 0;
    font-family: "Poppins", sans-serif; font-weight: 700; font-size: 64px; line-height: 1;
  }
  .legend-sub {
    position: absolute; left: 80px; top: 62px; margin: 0;
    font-family: "Quicksand", sans-serif; font-weight: 400; font-size: 35px; line-height: 1; white-space: nowrap;
  }
  .legend--hero { top: 770px; color: var(--hero); }
  .legend--hub { top: 894px; color: var(--hub); }
  .legend--hygiene { top: 1014px; color: var(--hygiene); }
  .legend--hero .legend-swatch, .legend--hero .legend-rule { background: var(--hero); }
  .legend--hub .legend-swatch, .legend--hub .legend-rule { background: var(--hub); }
  .legend--hygiene .legend-swatch, .legend--hygiene .legend-rule { background: var(--hygiene); }
</style>
</head>
<body>
<main class="canvas">
  <svg class="funnel-diagram" width="958" height="720" viewBox="0 0 958 720" aria-label="Sales content funnel">
    <defs>
      <marker id="arrowhead" viewBox="0 0 10 10" refX="8" refY="5" markerWidth="4" markerHeight="4" orient="auto">
        <path d="M0 0 L10 5 L0 10 Z" fill="var(--ink)"/>
      </marker>
    </defs>

    <!-- funnel bands -->
    <polygon class="band band--sales" points="46,174 698,174 636,294 108,294" fill="var(--red)"/>
    <polygon class="band band--awareness" points="108,294 636,294 574,414 170,414" fill="var(--orange)"/>
    <polygon class="band band--consideration" points="170,414 574,414 514,534 232,534" fill="var(--green)"/>
    <polygon class="band band--action" points="232,534 514,534 452,662 292,662" fill="var(--blue)"/>
    <polygon class="funnel-highlight" points="46,174 90,174 298,662 292,662" fill="#fff" opacity="0.3"/>
    <polygon class="funnel-shade" points="572,174 698,174 452,662 412,662" fill="#000" opacity="0.06"/>

    <!-- funnel text -->
    <text class="heading" x="381" y="248" font-size="82" text-anchor="middle">SALES</text>
    <text class="heading" x="381" y="284" font-size="26" font-weight="700" text-anchor="middle">Content Funnel</text>

    <text class="heading" x="378" y="338" font-size="50" text-anchor="middle">AWARENESS</text>
    <text class="kicker" x="378" y="357" font-size="16" fill="var(--brown)" text-anchor="middle">IDENTIFY PROBLEM/NEED</text>
    <text class="point" x="378" y="376" font-size="15" fill="#fff" text-anchor="middle">• Aspirational</text>
    <text class="point" x="384" y="402" font-size="15" fill="#fff" text-anchor="middle">• Market The <tspan text-decoration="underline">Outcome</tspan> Not Product</text>

    <text class="heading" x="376" y="446" font-size="36" text-anchor="middle">CONSIDERATION</text>
    <text class="kicker" x="374" y="466" font-size="16" fill="var(--deep-green)" text-anchor="middle">EVALUATE ALTERNATIVES</text>
    <text class="point" x="376" y="487" font-size="15" fill="#fff" text-anchor="middle">•Why is <tspan text-decoration="underline">this solution</tspan> better than others</text>
    <text class="point" x="376" y="507" font-size="15" fill="#fff" text-anchor="middle">•<tspan text-decoration="underline">How</tspan> is the provider going to solve</text>
    <text class="point" x="378" y="523" font-size="15" fill="#fff" text-anchor="middle">my need</text>

    <text class="heading" x="373" y="562" font-size="22" font-weight="700" text-anchor="middle">ACTION/DECISION</text>
    <text class="kicker" x="373" y="579" font-size="13" fill="var(--deep-blue)" text-anchor="middle">PRESENT AN OFFER</text>
    <text class="point" x="373" y="604" font-size="15" fill="#fff" text-anchor="middle">•<tspan text-decoration="underline">Which</tspan> Provider?</text>

    <!-- content type tags -->
    <polygon class="tag tag--problem" points="640,306 878,306 832,402 614,402" fill="var(--orange)"/>
    <text class="tag-title" x="755" y="334" font-size="20" fill="var(--brown)" text-anchor="middle">Problem &amp; Solution</text>
    <text class="point" x="732" y="360" font-size="16" fill="#fff" text-anchor="middle">• Subject Showing</text>
    <text class="point" x="735" y="379" font-size="16" fill="#fff" text-anchor="middle">Symptons of Problems</text>

    <polygon class="tag tag--providers" points="592,442 814,442 770,532 554,532" fill="var(--green)"/>
    <text class="tag-title" x="696" y="464" font-size="20" fill="var(--deep-green)" text-anchor="middle">Providers &amp; Types of</text>
    <text class="tag-title" x="696" y="482" font-size="20" fill="var(--deep-green)" text-anchor="middle">Solution</text>
    <text class="point" x="574" y="506" font-size="16" fill="#fff">•Subject Gives</text>
    <text class="point" x="568" y="525" font-size="16" fill="#fff">Name to Problem</text>

    <polygon class="tag tag--convert" points="530,575 754,575 734,615 515,615" fill="var(--blue)"/>
    <text class="tag-title" x="634" y="600" font-size="20" fill="var(--deep-blue)" text-anchor="middle">Convert &amp; Retain</text>

    <polygon class="tag tag--referral" points="492,654 668,654 656,685 483,685" fill="var(--purple)"/>
    <text class="tag-title" x="574" y="673" font-size="16" fill="#fff" text-anchor="middle">Wom &amp; Referral</text>

    <!-- flow arrows -->
    <g class="flow" fill="none" stroke="var(--ink)" stroke-width="7" stroke-linecap="round" marker-end="url(#arrowhead)">
      <path d="M666 662 L770 660 C815 656 812 602 758 593"/>
      <path d="M764 592 C870 578 872 486 814 480"/>
      <path d="M822 478 C926 462 924 362 862 350"/>
      <path d="M486 663 L452 662"/>
    </g>
  </svg>

  <section class="legend legend--hero">
    <span class="legend-swatch"></span>
    <h2 class="legend-title">Hero</h2>
    <p class="legend-sub">Tentpole Campaigns</p>
    <span class="legend-rule"></span>
  </section>
  <section class="legend legend--hub">
    <span class="legend-swatch"></span>
    <h2 class="legend-title">Hub</h2>
    <p class="legend-sub">Regular “Push” Content</p>
    <span class="legend-rule"></span>
  </section>
  <section class="legend legend--hygiene">
    <span class="legend-swatch"></span>
    <h2 class="legend-title">Hygiene</h2>
    <p class="legend-sub">Always-on “Pull” Content</p>
    <span class="legend-rule"></span>
  </section>
</main>
</body>
</html>
```